Mindfulness School for Children -- Business Cards

We're looking for business cards for our school directors and owners. We're a mindfulness school for children called little lanterns. Attached are our logos/icons.

```html
<!DOCTYPE html>
<html lang="en">
<head>
<meta charset="utf-8">
<title>little lanterns — Business Card</title>
<link href="https://fonts.googleapis.com/css2?family=Karla:wght@400;500;700&display=swap" rel="stylesheet">
<style>
  :root {
    --backdrop: #8f8f8f;
    --paper: #ffffff;
    --teal: #4aa8c0;
    --sage: #6cb49a;
    --ink: #4f4f4f;
    --icon: #6fb89e;
    --band: #7cc3a0;
    --bloom-light: #7cc4d2;
    --bloom-dark: #3e9fb8;
    --pattern-light: #45e6f8;
    --pattern-mid: #2aa3bd;
    --pattern-dark: #0d5b82;
  }
  * { margin: 0; padding: 0; box-sizing: border-box; }
  html, body { width: 1200px; height: 1200px; overflow: hidden; }
  body {
    background: var(--backdrop);
    font-family: "Karla", Arial, sans-serif;
    position: relative;
  }
  .card {
    position: absolute;
    left: 257px;
    width: 686px;
    height: 392px;
    overflow: hidden;
  }
  .card-front { top: 160px; background: var(--paper); }
  .card-back { top: 648px; }

  .brand {
    position: absolute;
    left: 34px;
    top: 62px;
    font-size: 32px;
    font-weight: 500;
    color: var(--teal);
    display: flex;
    align-items: center;
    gap: 10px;
    letter-spacing: 0.2px;
  }
  .brand-dot {
    width: 12px; height: 12px;
    border-radius: 50%;
    background: var(--teal);
  }
  .person { position: absolute; left: 32px; top: 143px; }
  .person-name {
    font-size: 21px;
    font-weight: 700;
    color: var(--teal);
    letter-spacing: 1.4px;
  }
  .person-role { font-size: 14.5px; color: var(--sage); letter-spacing: 0.6px; }

  .address {
    position: absolute;
    left: 33px;
    top: 200px;
    font-size: 14px;
    line-height: 19px;
    color: var(--ink);
    letter-spacing: 0.5px;
  }
  .contacts {
    position: absolute;
    left: 33px;
    top: 248px;
    list-style: none;
    font-size: 14px;
    color: var(--ink);
    letter-spacing: 0.5px;
  }
  .contacts li { display: flex; align-items: center; height: 19.4px; gap: 9px; }
  .contacts svg { width: 13px; height: 13px; fill: var(--icon); flex: none; }

  .accent-band {
    position: absolute;
    left: 0; bottom: 0;
    width: 410px; height: 9px;
    background: var(--band);
    clip-path: polygon(0 0, 94% 0, 100% 100%, 0 100%);
  }
  .bloom-art {
    position: absolute;
    left: 348px; top: 40px;
    width: 338px; height: 352px;
    border-radius: 60% 0 0 0;
    background: radial-gradient(circle at 60% 45%, var(--bloom-light), var(--bloom-dark));
    opacity: 0.85;
  }

  .pattern-art {
    position: absolute; inset: 0;
    background: linear-gradient(100deg, var(--pattern-light) 0%, var(--pattern-mid) 50%, var(--pattern-dark) 100%);
  }
  .back-name {
    position: absolute;
    left: 488px; top: 328px;
    font-size: 20px;
    font-weight: 500;
    color: #ffffff;
  }
</style>
</head>
<body>
  <section class="card card-front">
    <div class="brand"><span>little lanterns</span><span class="brand-dot"></span></div>

    <div class="person">
      <div class="person-name">DANIEL REYES</div>
      <div class="person-role">President</div>
    </div>

    <address class="address" style="font-style:normal">
      412 Willow Bend Road<br>
      Juneau, Alaska 99801
    </address>

    <ul class="contacts">
      <li>
        <svg viewBox="0 0 16 16"><path d="M3.6 1.2l2.3 2.4-1.2 2a9 9 0 0 0 5.7 5.7l2-1.2 2.4 2.3-1.6 2.3C7.6 14.4 1.6 8.4 1.3 2.8z"/></svg>
        555-214-7730
      </li>
      <li>
        <svg viewBox="0 0 16 16"><path d="M4.5 0.5h7a1 1 0 0 1 1 1v13a1 1 0 0 1-1 1h-7a1 1 0 0 1-1-1v-13a1 1 0 0 1 1-1zm.8 2v10h5.4v-10zm2 11h1.4v1H7.3z"/></svg>
        555-318-6042
      </li>
      <li>
        <svg viewBox="0 0 16 16"><path d="M4 1h7l1 1v4H4zM1 7h14v6h-2v-2H3v2H1zm3 5h8v3H4z"/></svg>
        555-427-9185
      </li>
      <li>
        <svg viewBox="0 0 16 16"><path d="M1 3h14v10H1zm1.5 1.2v.4L8 8.6l5.5-4v-.4z"/></svg>
        hello@littlelanterns.com
      </li>
      <li>
        <svg viewBox="0 0 16 16"><circle cx="8" cy="8" r="7"/><path d="M4 5c2 0 3 1 2.5 3S8 10 7 13M10 2.5c-1 1.5 0 3 2 3.5" stroke="#fff" stroke-width="1.2" fill="none"/></svg>
        www.littlelanterns.com
      </li>
    </ul>

    <div class="accent-band"></div>
    <div class="bloom-art" role="img" aria-label="Large watercolour flower decoration in soft teal"></div>
  </section>

  <section class="card card-back">
    <div class="pattern-art" role="img" aria-label="Repeating embossed flower pattern shading from bright cyan to deep blue"></div>
    <div class="back-name">little lanterns</div>
  </section>
</body>
</html>
```